Business Card Design for Marketing Firm

Looking for business card design for higher end marketing firm. Clean but impressionable/trendy. We are a marketing firm that represents manufacturers in the foodservice equipment and supply industry. Our customers are end users such has hotels, restaurants, country clubs, convention centers and casinos as well as distributors of restaurants supplies and equipment, and manufacturers of foodservice equipment and supplies.
Target Market(s)
Hotels, Restaurants, Supply & Equipment Distributors, Foodservice Manufacturers
Industry/Entity Type
Foodservice/Hospitality
Contact Information for Business Card
Name, Title, Contact Number, Email, Website, Social Media, Address
Requirements
Must have
- Clean & Simple but Serious and Impressionable

```html
<!DOCTYPE html>
<html lang="en">
<head>
<meta charset="utf-8">
<title>Larkfield Partners — Business Card</title>
<link rel="stylesheet" href="https://fonts.googleapis.com/css2?family=Libre+Baskerville:wght@700&family=Arimo:wght@400;700&display=swap">
<style>
  :root {
    --navy: #020a73;
    --paper: #f4f4f6;
    --white: #ffffff;
    --stage: #7d7d7d;
  }
  * { box-sizing: border-box; margin: 0; padding: 0; }
  html, body { width: 1200px; height: 900px; overflow: hidden; }
  body {
    background: var(--stage);
    position: relative;
    font-family: "Arimo", Arial, sans-serif;
  }
  .card {
    position: absolute;
    width: 640px;
    height: 366px;
    border-radius: 26px;
  }
  .card--front {
    left: 140px; top: 70px;
    background: var(--paper);
    color: var(--navy);
    display: flex;
    flex-direction: column;
    align-items: center;
    justify-content: center;
  }
  .card--back {
    left: 420px; top: 470px;
    background: var(--navy);
    color: var(--white);
  }
  .brand {
    display: flex;
    align-items: center;
    gap: 16px;
  }
  .brand__emblem {
    flex: none;
    width: 52px; height: 52px;
    border: 3px solid var(--navy);
    border-radius: 50%;
  }
  .brand__name {
    font-family: "Arimo", Arial, sans-serif;
    font-weight: 400;
    font-size: 32px;
    white-space: nowrap;
  }
  .website {
    margin-top: 34px;
    font-size: 13px;
    letter-spacing: 4px;
  }
  .social {
    position: absolute;
    right: 34px; top: 24px;
    display: flex;
    gap: 5px;
  }
  .social__dot {
    width: 20px; height: 20px;
    border-radius: 50%;
    background: var(--white);
  }
  .back-mark {
    position: absolute;
    left: 60px; top: 158px;
    display: flex;
    align-items: center;
    gap: 12px;
  }
  .back-mark__emblem {
    flex: none;
    width: 46px; height: 46px;
    border: 3px solid var(--white);
    border-radius: 50%;
  }
  .back-mark__name {
    font-family: "Arimo", Arial, sans-serif;
    font-weight: 400;
    font-size: 22px;
    white-space: nowrap;
  }
  .contact {
    position: absolute;
    left: 370px; top: 96px;
    font-size: 15px;
    line-height: 1.3;
  }
  .contact__name {
    font-family: "Libre Baskerville", serif;
    font-weight: 700;
    font-size: 21px;
    letter-spacing: 0.5px;
  }
  .contact__title { margin-bottom: 10px; margin-left: 10px; }
  .contact__address { margin-left: 20px; margin-bottom: 10px; }
  .contact__lines { list-style: none; margin-left: 40px; }
  .contact__label { font-weight: 700; display: inline-block; width: 28px; }
</style>
</head>
<body>
  <section class="card card--front" aria-label="Business card front">
    <div class="brand">
      <span class="brand__emblem" aria-hidden="true"></span>
      <span class="brand__name">Larkfield Partners</span>
    </div>
    <p class="website">www.LARKFIELD.com</p>
  </section>

  <section class="card card--back" aria-label="Business card back">
    <div class="social" aria-label="Social media">
      <span class="social__dot"></span>
      <span class="social__dot"></span>
      <span class="social__dot"></span>
    </div>
    <div class="back-mark">
      <span class="back-mark__emblem" aria-hidden="true"></span>
      <span class="back-mark__name">Larkfield Partners</span>
    </div>
    <div class="contact">
      <p class="contact__name">DANIEL CARTER</p>
      <p class="contact__title">President</p>
      <p class="contact__address">1427 Linden Avenue<br>Maple Grove, NY 11050</p>
      <ul class="contact__lines">
        <li><span class="contact__label">P :</span>(555) 0142-7788</li>
        <li><span class="contact__label">E :</span>name@LARKFIELD.com</li>
        <li><span class="contact__label">W :</span>www.LARKFIELD.com</li>
      </ul>
    </div>
  </section>
</body>
</html>
```